Australian based company requires brochure design for new safety product.

New company with no Logo or branding - Let your imagination run wild.

Varnoth Pty Ltd need a brochure designed for marketing a safety product.
The idea of the brochure is to leave with Procurement departments of the health and safety industry for quick easy reference of product specifications and benefits.

Target Market(s)

Procurement teams of Health and Safety Industry. Quick easy reference points of specifications and benefits of product.

Industry/Entity Type

Marketing

Requirements
Must have
• Must have product details and specifications as per below, preferred format A4 sheet, front to back, with attached 6 photos, as well JPEG drawing attached.

With Government legislation a requirement all electrical cords be elevated a minimum of 2 meters on construction sites - THE BRIXOM STAND was developed.
With over thirty years experience in the construction industry and safety requirements that continue to evolve we have designed and developed a lead stand that is ergonomic, portable and versatile. With no other product like it on the market.

BENEFITS
- Unique portable and easy to assemble Brixomrig to fit in most tool boxes
- Non-conductive and highly visible
- Indoor and outdoor use
- Leads the way in working safely
- Complies with Government legislation
- Construction sites, Outdoor events and Camping grounds

FUNCTIONS
- Fully adjustable Telescopic Brixomrig from 1.2 meters to 4.2 meters
- Spring loaded to lock between two surfaces
- Supports multiple leads, including temporary lighting and can also be used for Laser levels
- Can be screwed to a wall to elevate above floor finishes

For all enquires please contact varnoth@examplemail.net or Dorit Famberg 0498356021

```html
<!DOCTYPE html>
<html lang="en">
<head>
<meta charset="utf-8">
<title>The Brixom Stand</title>
<link rel="stylesheet" href="https://fonts.googleapis.com/css2?family=Archivo+Black&family=Roboto+Condensed:wght@400;700&display=swap">
<style>
  :root {
    --charcoal: #333333;
    --panel: #4b4b4b;
    --title-ink: #2b2b2b;
    --sky-top: #9ea3a8;
    --sky-mid: #d8dde2;
    --sky-low: #f4f7fa;
    --lime: #9cc731;
    --brown: #4e3426;
    --ice: #bfe4f4;
    --white: #ffffff;
  }
  html, body { margin: 0; padding: 0; overflow: hidden; background: var(--charcoal); }
  .brochure {
    position: relative;
    width: 848px;
    height: 1200px;
    overflow: hidden;
    background: var(--charcoal);
    font-family: "Roboto Condensed", Arial, sans-serif;
  }
  .hero-backdrop {
    position: absolute; inset: 0 0 auto 0; height: 560px;
    background: linear-gradient(180deg, var(--sky-top) 0%, #c3c7cc 12%, #7c8288 22%, var(--sky-mid) 34%, #a9aeb3 46%, var(--sky-low) 62%, #e6eef4 80%);
  }
  .wave { position: absolute; left: 0; top: 0; width: 848px; height: 1200px; }
  .title {
    position: absolute; top: 62px; left: 0; width: 100%;
    margin: 0; text-align: center;
    font-family: "Archivo Black", Arial, sans-serif;
    font-size: 45px; letter-spacing: 1px;
    color: var(--title-ink);
    -webkit-text-stroke: 1.5px var(--white);
    paint-order: stroke fill;
    text-shadow: 0 0 4px rgba(255,255,255,.8);
  }
  .product-render {
    position: absolute; left: 80px; top: 150px; width: 705px; height: 220px;
    background: linear-gradient(160deg, rgba(60,150,60,.25), rgba(200,190,60,.25));
    border-radius: 6px;
  }
  .tagline {
    position: absolute; top: 398px; left: 232px; margin: 0;
    font-size: 29px; color: var(--charcoal); word-spacing: 4px;
  }
  .intro-panel {
    position: absolute; left: 28px; top: 578px; width: 792px; height: 378px;
    background: var(--panel); border-radius: 3px;
    box-sizing: border-box; padding: 22px 40px 0;
    color: var(--white); text-align: center;
    font-size: 30px; line-height: 36px;
  }
  .intro-panel p { margin: 0 0 6px; }
  .contact {
    position: absolute; top: 1012px; left: 0; width: 100%;
    text-align: center; color: var(--white);
    font-size: 29px; line-height: 44px;
  }
  .contact p { margin: 0; }
  .contact .call { font-weight: 700; font-size: 33px; margin-top: 4px; }
  .contact .call .gap { display: inline-block; width: 18px; }
</style>
</head>
<body>
<main class="brochure">
  <div class="hero-backdrop"></div>
  <svg class="wave" viewBox="0 0 848 1200" aria-hidden="true">
    <path d="M0,430 C220,470 470,470 848,360 L848,392 C520,500 240,500 0,448 Z" fill="var(--ice)"/>
    <path d="M120,446 C380,480 620,440 848,372 L848,430 C600,508 340,500 120,446 Z" fill="var(--brown)"/>
    <path d="M0,452 C260,505 560,515 848,430 L848,452 C560,540 260,530 0,470 Z" fill="var(--lime)"/>
    <path d="M0,466 C260,526 560,536 848,448 L848,1200 L0,1200 Z" fill="var(--charcoal)"/>
  </svg>

  <h1 class="title">THE BRIXOM STAND</h1>
  <div class="product-render" role="img" aria-label="3D render of the telescopic green stand with yellow end plates and lead hooks, plus a ground spike"></div>
  <p class="tagline">Ergonomic &gt;&gt; Portable &gt;&gt; Versatile</p>

  <section class="intro-panel">
    <p>With Government legislation a requirement all electrical cords be elevated a minimum of 2 meters on construction sites - THE BRIXOM STAND was developed.</p>
    <p>With over thirty years experience in the construction industry and safety requirements that continue to evolve we have designed and developed a lead stand that is ergonomic, portable and versatile. With no other product like it on the market.</p>
  </section>

  <section class="contact">
    <p>For all enquires please contact</p>
    <p>varnoth@examplemail.net</p>
    <p class="call">or call<span class="gap"></span> Dorit Famberg 0498356021</p>
  </section>
</main>
</body>
</html>
```